7:40 Command Blueprint- A Handbook To Shape The Captain Others Could Trust

7:40 Command Blueprint
A Handbook To Shape The Captain Others Could Trust

It will be a 6 X 9 guide that is meant for people to keep with them with pages to fill out. See supporting pics for overall pillars that are discussed and form basis of the solution.

I will need a spine and back cover as well.

My blog and content: www.corvinmhale-example.com

Target Market(s)

Business professionals, senior emergency services people

Industry/Entity Type

Business Management

Font styles to use
Serif

Colors

Designer to choose colors to be used in the design.

Requirements
Must have
• Clean look, easily recognizable among other books. Front cover and back and spine. My picture on the back somewhere (corner maybe?!)
Nice to have
• Easily recognizeable
• NOTE: Graphic should read Today, Was I the Leader That I Would Want? I uploaded graphic that says ..."I Would've Wanted" which is incorrect.
Should not have
• Busy cover

```html
<!DOCTYPE html>
<html lang="en">
<head>
<meta charset="utf-8">
<title>7:40 Command Blueprint — Book Cover Wrap</title>
<link rel="stylesheet" href="https://fonts.googleapis.com/css2?family=Oswald:wght@400;500;600&family=Arimo:wght@400&display=swap">
<style>
  :root {
    --stage: #000000;
    --paper: #f7f7f7;
    --paper-shade: #e9e9ea;
    --title-blue: #1b4f9e;
    --ink: #1f1f1f;
    --ink-soft: #3a3a3a;
    --rule: #7a7a7a;
    --pattern-light: #f3f4f6;
    --pattern-mid: #d6d9df;
    --placeholder: #dcdde1;
  }
  * { box-sizing: border-box; margin: 0; padding: 0; }
  html, body { width: 1200px; height: 1200px; overflow: hidden; background: var(--stage); }
  .canvas { position: relative; width: 1200px; height: 1200px; background: var(--stage); }

  .book-wrap {
    position: absolute; left: 57px; top: 240px; width: 1079px; height: 722px;
    background: radial-gradient(ellipse at 78% 40%, #ffffff 0%, var(--paper) 45%, var(--paper-shade) 100%);
    overflow: hidden;
  }

  .boat-field {
    position: absolute; left: 0; top: 560px; width: 100%; height: 110px;
    background: linear-gradient(180deg, rgba(255,255,255,0) 0%, var(--pattern-mid) 45%, var(--pattern-light) 100%);
    opacity: .75;
  }

  /* Back cover */
  .back-cover { position: absolute; left: 0; top: 0; width: 498px; height: 100%; }
  .back-title {
    position: absolute; left: 36px; top: 22px;
    font: 600 36px/1 "Oswald", sans-serif; color: var(--title-blue); letter-spacing: .3px;
  }
  .back-copy {
    position: absolute; left: 36px; width: 444px;
    font: 400 12.5px/17px "Arimo", sans-serif; color: var(--ink); text-align: justify;
  }
  .back-copy.intro { top: 78px; }
  .back-copy.detail { top: 202px; }
  .back-rule { position: absolute; left: 36px; top: 435px; width: 444px; border-top: 1px solid var(--rule); }
  .author-photo {
    position: absolute; left: 36px; top: 460px; width: 102px; height: 136px;
    background: linear-gradient(160deg, #2a2a2a, #0a0a0a);
  }
  .back-copy.bio { top: 458px; left: 153px; width: 327px; }
  .back-url {
    position: absolute; left: 36px; top: 688px;
    font: 400 12.5px/1 "Arimo", sans-serif; color: var(--ink-soft);
  }

  /* Spine */
  .spine { position: absolute; left: 498px; top: 0; width: 75px; height: 100%; }
  .spine-text {
    position: absolute; left: 50%; transform: translateX(-50%);
    writing-mode: vertical-rl; white-space: nowrap;
  }
  .spine-title { top: 28px; font: 600 34px/1 "Oswald", sans-serif; color: var(--title-blue); }
  .spine-author { top: 555px; font: 400 17px/1 "Oswald", sans-serif; color: var(--ink); letter-spacing: .5px; }

  /* Front cover */
  .front-cover { position: absolute; left: 573px; top: 0; width: 506px; height: 100%; }
  .front-title {
    position: absolute; left: 0; top: 20px; width: 100%; text-align: center;
    font: 500 97px/97px "Oswald", sans-serif; color: var(--title-blue); letter-spacing: 1px;
  }
  .front-subtitle {
    position: absolute; left: 40px; top: 320px; width: 436px;
    border-top: 1px solid var(--rule); border-bottom: 1px solid var(--rule);
    padding: 7px 0 6px; text-align: center; white-space: nowrap;
    font: 400 10px/1.2 "Arimo", sans-serif; color: var(--ink-soft);
  }
  .compass-art {
    position: absolute; left: 307px; top: 465px; width: 97px; height: 97px; border-radius: 50%;
    background: radial-gradient(circle, #e8e9ec 0%, var(--placeholder) 100%);
  }
  .front-author {
    position: absolute; left: 0; top: 663px; width: 100%; text-align: center;
    font: 400 26px/1 "Oswald", sans-serif; color: var(--ink); letter-spacing: .6px;
  }
</style>
</head>
<body>
<div class="canvas">
  <div class="book-wrap">
    <div class="boat-field" role="img" aria-label="Rows of small white paper boats across the lower cover"></div>

    <section class="back-cover">
      <h2 class="back-title">7:40 COMMAND BLUEPRINT</h2>
      <p class="back-copy intro">Lorem ipsum dolor sit amet, consectetur adipiscing elit, sed do eiusmod tempor incididunt ut labore et dolore magna aliqua. Ut enim ad minim veniam, quis nostrud exercitation ullamco laboris nisi ut aliquip ex ea commodo consequat. Duis aute irure dolor in reprehenderit in voluptate velit esse cillum dolore eu fugiat nulla pariatur. Excepteur sint occaecat cupidatat non proident, sunt in culpa qui officia deserunt mollit anim id est laborum.</p>
      <p class="back-copy detail">Sed ut perspiciatis unde omnis iste natus error sit voluptatem accusantium doloremque laudantium, totam rem aperiam, eaque ipsa quae ab illo inventore veritatis et quasi architecto beatae vitae dicta sunt explicabo. Nemo enim ipsam voluptatem quia voluptas sit aspernatur aut odit aut fugit, sed quia consequuntur magni dolores eos qui ratione voluptatem sequi nesciunt. Neque porro quisquam est, qui dolorem ipsum quia dolor sit amet, consectetur, adipisci velit, sed quia non numquam eius modi tempora incidunt ut labore et dolore magnam aliquam quaerat voluptatem. Ut enim ad minima veniam, quis nostrum exercitationem ullam corporis suscipit laboriosam, nisi ut aliquid ex ea commodi consequatur? Quis autem vel eum iure reprehenderit qui in ea voluptate velit esse quam nihil molestiae consequatur, vel illum qui dolorem eum fugiat quo voluptas nulla pariatur?</p>
      <div class="back-rule"></div>
      <div class="author-photo" role="img" aria-label="Author portrait"></div>
      <p class="back-copy bio">Lorem ipsum dolor sit amet, consectetur adipiscing elit, sed do eiusmod tempor incididunt ut labore et dolore magna aliqua. Ut enim ad minim veniam, quis nostrud exercitation ullamco laboris nisi ut aliquip ex ea commodo consequat. Duis aute irure dolor in reprehenderit in voluptate velit esse cillum dolore eu fugiat nulla pariatur. Excepteur sint occaecat cupidatat non proident, sunt in culpa qui officia deserunt mollit anim id est laborum.</p>
      <p class="back-url">www.corvinmhale-example.com</p>
    </section>

    <section class="spine">
      <span class="spine-text spine-title">7:40 COMMAND BLUEPRINT</span>
      <span class="spine-text spine-author">CORVIN M. HALE</span>
    </section>

    <section class="front-cover">
      <h1 class="front-title">7:40<br>COMMAND<br>BLUEPRINT</h1>
      <p class="front-subtitle">A PRACTICAL HANDBOOK TO SHAPE THE CAPTAIN OTHERS COULD TRUST</p>
      <div class="compass-art" role="img" aria-label="Compass illustration with a trailing path"></div>
      <p class="front-author">CORVIN M. HALE</p>
    </section>
  </div>
</div>
</body>
</html>
```